Hollis Valley Winery needs a fresh label design for new line of natural wines

The growing natural wine market requires a fresh perspective. Traditional wine labels don't attract the attention of natural wine buyers or the spirit for which they were made. Natural wines tend to be sustainable, organic and biodynamic. Natural wines also break norms and have disrupted the commercial wine industry with their non-traditional imagery and label designs. Natural wines stick out on the shelf for their brighter colors, illustrations and more handwritten font selections. Bottles are typically flint (clear glass) showing the true color of the wine, red and white. Red wines are typically not opaque, but rather light colored with zero filtration (
see attached pic). No capsule is used, therefore, the cork is shown through the glass bottle.

Target Market(s)

Wine buyers between the ages of 21-35 generally living in large cities, but more specifically San Francisco and Los Angeles

Requirements
Must have
• Dimensions:2 3/4 Inches Wide5 1/4 Inches TallIntended to print on Bright White Felt paper CMYK
Nice to have
• It may not have any words on the front label at all. It's more about symbolism and color and design then it is about the actual brand name (which will go on the back where all the legal stuff is). I've included several bottle shots from natural winemakers that may give you a sense that there is no one way to design a natural wine label, but rather several directions at this early stage in the market cycle
Should not have
• If it looks and smells like a traditional wine label, it's probably not the right idea

```html
<!DOCTYPE html>
<html lang="en">
<head>
<meta charset="utf-8">
<title>Hollis Valley Winery – Natural Wine Label</title>
<link href="https://fonts.googleapis.com/css2?family=Montserrat:wght@300;400&display=swap" rel="stylesheet">
<style>
  :root {
    --page-bg: #ffffff;
    --trim-line: #9a9a9a;
    --label-stock: #ffffff;
    --label-red: #e6202b;
    --label-red-deep: #de1a28;
    --label-orange: #ee4a1c;
    --label-amber: #f2781a;
    --label-gold: #f6a51c;
    --type-white: #ffffff;
  }

  * { box-sizing: border-box; margin: 0; padding: 0; }

  html, body {
    width: 1200px;
    height: 1200px;
    overflow: hidden;
    background: var(--page-bg);
  }

  .canvas {
    position: relative;
    width: 1200px;
    height: 1200px;
  }

  .label {
    position: absolute;
    left: 345px;
    top: 70px;
    width: 510px;
    height: 1060px;
    background: var(--label-stock);
    border: 1.5px solid var(--trim-line);
    padding: 30px;
  }

  .label-face {
    position: relative;
    width: 100%;
    height: 100%;
    overflow: hidden;
    background: var(--label-red);
  }

  .forest-artwork {
    position: absolute;
    inset: 0;
    background:
      radial-gradient(ellipse 30% 22% at 22% 8%, var(--label-gold) 0%, rgba(246,165,28,0) 100%),
      radial-gradient(ellipse 45% 35% at 25% 18%, var(--label-amber) 0%, rgba(242,120,26,0) 100%),
      radial-gradient(ellipse 35% 50% at 85% 30%, rgba(238,74,28,0.8) 0%, rgba(238,74,28,0) 100%),
      linear-gradient(180deg, var(--label-orange) 0%, var(--label-red) 45%, var(--label-red-deep) 100%);
  }

  .winery-name {
    position: absolute;
    left: 86px;
    top: 770px;
    color: var(--type-white);
    font-family: "Montserrat", sans-serif;
    font-weight: 300;
    line-height: 1;
  }

  .winery-name .name-line {
    display: block;
    font-size: 56px;
    letter-spacing: 1px;
    line-height: 66px;
  }

  .winery-name .descriptor {
    display: block;
    margin-top: 6px;
    font-size: 26px;
    letter-spacing: 17px;
    font-weight: 400;
  }
</style>
</head>
<body>
  <main class="canvas">
    <section class="label" aria-label="Front wine label, 2.75 by 5.25 inches">
      <div class="label-face">
        <div class="forest-artwork" role="img" aria-label="Redwood forest photograph toned in red and orange, with sunlight glowing through the tall trunks"></div>
        <h1 class="winery-name">
          <span class="name-line">HOLLIS</span>
          <span class="name-line">VALLEY</span>
          <span class="descriptor">WINERY</span>
        </h1>
      </div>
    </section>
  </main>
</body>
</html>
```